Local fast-growing company in the service sector

We are looking for a modern business card design, which should also appear on our letterheads

Target Market(s)

Private and industrial sectors

Contact Information for Business Card

Vorname Name
Kellberger Str. 18
73614 Lindenfeld
Tel.: 07146-839214-0
Name@agentur-kvtl.de

Colors
9d9d9d
919191
aaaaaa

Requirements
Must have
• The logo (file) in silver

```html
<!DOCTYPE html>
<html lang="de">
<head>
<meta charset="utf-8">
<title>KVTL Visitenkarte</title>
<link href="https://fonts.googleapis.com/css2?family=Roboto:wght@400;500&display=swap" rel="stylesheet">
<style>
  :root {
    --backdrop: #2e2e2e;
    --card: #ffffff;
    --frame: #8a8a8a;
    --silver: #9d9d9d;
    --silver-light: #aaaaaa;
    --ink: #1e1e1e;
    --rule: #3a3a3a;
  }
  html, body {
    margin: 0;
    width: 1200px;
    height: 1200px;
    overflow: hidden;
    background: var(--backdrop);
    font-family: "Roboto", sans-serif;
  }
  .business-card {
    position: absolute;
    left: 100px;
    top: 315px;
    width: 1000px;
    height: 570px;
    background: var(--card);
    border-radius: 48px 0 48px 0;
    overflow: hidden;
  }
  .card-frame {
    position: absolute;
    inset: 0;
  }
  .ornament {
    position: absolute;
    width: 122px;
    height: 118px;
    background: radial-gradient(circle at var(--o), #9a9a9a 0%, #c8c8c8 45%, rgba(255,255,255,0) 75%);
    opacity: .8;
  }
  .ornament--top-left { left: 14px; top: 16px; --o: 20% 20%; }
  .ornament--bottom-right { right: 18px; bottom: 24px; --o: 80% 80%; }
  .brand {
    position: absolute;
    left: 93px;
    top: 96px;
    display: flex;
    align-items: center;
    gap: 18px;
    color: var(--silver);
  }
  .brand-mark {
    width: 70px;
    height: 70px;
    background: var(--silver-light);
  }
  .brand-name {
    font-size: 78px;
    font-weight: 500;
    line-height: 1;
    letter-spacing: 2px;
  }
  .brand-url {
    position: absolute;
    left: 181px;
    top: 180px;
    font-size: 21px;
    font-weight: 500;
    letter-spacing: 1px;
    color: var(--silver);
  }
  .contact {
    position: absolute;
    left: 401px;
    color: var(--ink);
    white-space: nowrap;
  }
  .contact-name { top: 270px; font-size: 37px; }
  .contact-role { font-size: 23px; color: var(--silver-light); }
  .contact-address { top: 343px; font-size: 23px; }
  .contact-phone { top: 408px; font-size: 23px; }
  .contact-email { top: 451px; font-size: 23px; color: var(--silver-light); }
  .contact-web { left: 739px; top: 450px; font-size: 21px; }
  .contact-rule {
    position: absolute;
    left: 385px;
    width: 577px;
    height: 1px;
    background: var(--rule);
  }
  .contact-rule--first { top: 334px; }
  .contact-rule--second { top: 396px; }
</style>
</head>
<body>
  <div class="business-card">
    <svg class="card-frame" width="1000" height="570" viewBox="0 0 1000 570">
      <g stroke="var(--frame)" stroke-width="2" fill="none">
        <line x1="0" y1="23" x2="1000" y2="23"/>
        <line x1="0" y1="29" x2="1000" y2="29"/>
        <line x1="0" y1="540" x2="1000" y2="540"/>
        <line x1="0" y1="547" x2="1000" y2="547"/>
        <line x1="17" y1="0" x2="17" y2="570"/>
        <line x1="24" y1="0" x2="24" y2="570"/>
        <line x1="966" y1="0" x2="966" y2="570"/>
        <line x1="973" y1="0" x2="973" y2="570"/>
      </g>
    </svg>
    <div class="ornament ornament--top-left" role="img" aria-label="Verziertes Eckornament in Silbergrau"></div>
    <div class="ornament ornament--bottom-right" role="img" aria-label="Verziertes Eckornament in Silbergrau"></div>

    <div class="brand">
      <span class="brand-mark"></span>
      <span class="brand-name">KVTL</span>
    </div>
    <div class="brand-url">agentur-kvtl.de</div>

    <div class="contact contact-name">Vorname Name <span class="contact-role">| Position</span></div>
    <div class="contact-rule contact-rule--first"></div>
    <div class="contact contact-address">Kellberger Str. 18, 73614 Lindenfeld</div>
    <div class="contact-rule contact-rule--second"></div>
    <div class="contact contact-phone">Phone 07146-839214-0</div>
    <div class="contact contact-email">Name@agentur-kvtl.de</div>
    <div class="contact contact-web">agentur-kvtl.de</div>
  </div>
</body>
</html>
```